Business card for a Exhibition booth fabrication company

Hi. My company would like to change our corporate name card. We are an events and Exhibition stand builder company. We would like our corporate name card to resonate what we do. I need someone to create something unique that relates to the industry that I am in. The graphic designer should be creative to incorporate the elements of my industry and try to blend in well in the design of the card. Our aim is to ensure that we are unique and our card can look different from our competitors.
Updates

Target Market(s)

Marketing and events manager from all companies

Contact Information for Business Card

The business card should have the following details:
Name
Job Title
Email
Website

Colors

Designer to choose colors to be used in the design.

Requirements
Must have
• The card must be look something that is relevant to the service that I am providing. My website is: www.velmora-buildworks.com
• You can see my website to get more information on what service that I am doing
Nice to have
• On the back of my card, I would like to have a globe image with the incorporation of my company logo. This is to indicate that my services can be done in any part of the world.

```html
<!DOCTYPE html>
<html lang="en">
<head>
<meta charset="utf-8">
<title>Velmora Buildworks – Business Card</title>
<link rel="stylesheet" href="https://fonts.googleapis.com/css2?family=Arimo:wght@400;700&family=Montserrat:wght@600&family=Open+Sans:wght@400&display=swap">
<style>
  :root {
    --stage-light: #dcdde0;
    --stage-dark: #a2a4a7;
    --brand-red: #ec1c24;
    --map-red: #f2585d;
    --swoosh-grey: #626366;
    --text-grey: #58595b;
    --rule-grey: #b5b6b8;
    --paper: #ffffff;
    --card-edge: #8a8b8d;
  }
  * { margin: 0; padding: 0; box-sizing: border-box; }
  html, body { width: 1200px; height: 1118px; overflow: hidden; }
  body {
    position: relative;
    background: linear-gradient(90deg, var(--stage-light) 0%, #c9cacd 45%, var(--stage-dark) 100%);
    font-family: "Open Sans", Arial, sans-serif;
  }
  .card {
    position: absolute;
    width: 756px;
    height: 431px;
    border-radius: 28px;
    overflow: hidden;
  }
  .card-front { left: 230px; top: 98px; background: var(--paper); border: 1px solid var(--card-edge); }
  .card-back { left: 223px; top: 582px; background: var(--brand-red); }

  .front-header { position: absolute; inset: 0; }

  .holder {
    position: absolute;
    right: 34px;
    top: 20px;
    text-align: right;
    color: var(--paper);
    font-family: "Arimo", Arial, sans-serif;
  }
  .holder-name { font-size: 26px; font-weight: 700; letter-spacing: 0.3px; line-height: 34px; }
  .holder-title { font-size: 19px; font-weight: 400; letter-spacing: 0.5px; line-height: 28px; }

  .brand {
    position: absolute;
    display: flex;
    align-items: center;
    gap: 12px;
  }
  .front-brand { left: 33px; top: 214px; }
  .brand-mark { width: 28px; height: 28px; background: var(--brand-red); flex: none; }
  .brand-name {
    font-family: "Montserrat", Arial, sans-serif;
    font-weight: 600;
    font-size: 25px;
    letter-spacing: 2px;
    color: var(--text-grey);
    white-space: nowrap;
  }

  .contacts {
    position: absolute;
    left: 30px;
    top: 293px;
    font-size: 18px;
    color: var(--text-grey);
  }
  .contact-row { display: flex; align-items: center; height: 34px; }
  .contact-row svg { width: 19px; height: 19px; margin-right: 13px; flex: none; }

  .divider {
    position: absolute;
    left: 336px;
    top: 336px;
    width: 1px;
    height: 54px;
    background: var(--rule-grey);
  }
  .address {
    position: absolute;
    left: 357px;
    top: 327px;
    font-size: 18px;
    line-height: 34px;
    color: var(--text-grey);
  }

  .world-map {
    position: absolute;
    left: 0;
    top: 68px;
    width: 756px;
    height: 303px;
    background: radial-gradient(ellipse 60% 55% at 50% 48%, var(--map-red) 0%, rgba(242,88,93,0.75) 55%, rgba(236,28,36,0) 100%);
  }
  .back-brand {
    left: 0;
    right: 0;
    top: 273px;
    justify-content: center;
    gap: 14px;
  }
  .back-brand .brand-mark { width: 32px; height: 32px; background: var(--paper); }
  .back-brand .brand-name { color: var(--paper); font-size: 30px; letter-spacing: 3px; }
  .back-web {
    position: absolute;
    left: 0;
    right: 0;
    top: 390px;
    text-align: center;
    color: var(--paper);
    font-size: 19px;
    line-height: 26px;
    letter-spacing: 3px;
  }
</style>
</head>
<body>

<section class="card card-front">
  <svg class="front-header" width="756" height="431" viewBox="0 0 756 431" aria-hidden="true">
    <path d="M0 0 H756 V178 C600 100 400 55 0 70 Z" fill="var(--brand-red)"/>
    <path d="M0 70 C400 55 600 100 756 178 V218 C600 120 380 70 0 96 Z" fill="var(--swoosh-grey)"/>
    <path d="M0 80 C380 60 600 106 756 188 V198 C600 116 380 72 0 88 Z" fill="var(--paper)"/>
  </svg>

  <div class="holder">
    <p class="holder-name">DANIEL ARKWELL</p>
    <p class="holder-title">PRESIDENT</p>
  </div>

  <div class="brand front-brand">
    <span class="brand-mark"></span>
    <span class="brand-name">VELMORA BUILDWORKS</span>
  </div>

  <div class="contacts">
    <div class="contact-row">
      <svg viewBox="0 0 20 20" aria-hidden="true"><path d="M4 2 L7.5 2 L9 6 L7 7.5 C8 10 10 12 12.5 13 L14 11 L18 12.5 L18 16 C18 17 17 18 16 18 C8.5 17.5 2.5 11.5 2 4 C2 3 3 2 4 2 Z" fill="var(--brand-red)"/></svg>
      <span>014-555-0192</span>
    </div>
    <div class="contact-row">
      <svg viewBox="0 0 20 20" aria-hidden="true"><rect x="1.5" y="4" width="17" height="12" fill="var(--brand-red)"/><path d="M1.5 4 L10 11 L18.5 4" fill="none" stroke="#fff" stroke-width="1.5"/></svg>
      <span>info@velmora-buildworks.com</span>
    </div>
    <div class="contact-row">
      <svg viewBox="0 0 20 20" aria-hidden="true"><g fill="none" stroke="var(--brand-red)" stroke-width="1.6"><circle cx="10" cy="10" r="8"/><ellipse cx="10" cy="10" rx="3.5" ry="8"/><path d="M2 10 H18 M3.5 6 H16.5 M3.5 14 H16.5"/></g></svg>
      <span>www.velmora-buildworks.com</span>
    </div>
  </div>

  <div class="divider"></div>
  <div class="address">
    <p>Street Name, City Name</p>
    <p>Zipcode - 01234</p>
  </div>
</section>

<section class="card card-back">
  <div class="world-map" role="img" aria-label="World map in light red across the card, showing the company builds exhibition stands anywhere in the world"></div>
  <div class="brand back-brand">
    <span class="brand-mark"></span>
    <span class="brand-name">VELMORA BUILDWORKS</span>
  </div>
  <p class="back-web">www.velmora-buildworks.com</p>
</section>

</body>
</html>
```